RWT Fittings Ltd Business Cards

We need a business card with our business logo. We provide window and door installations on high-rises in west coast British Colombia, Canada.

I would like my business information and details on one side of the card, and the other side the company name with logo

Target Market(s)

General Contractors

Industry/Entity Type

Construction

Contact Information for Business Card

one side i want my company name and logo in the dark theme logo that i provided

Requirements
Must have
• Marco Peltieri, 16045518293, RWTFittings@mailbox-demo.com, 1407-5194 Linden Row Burnaby BC, V5H 2K9, Owner & Manager

```html
<!DOCTYPE html>
<html lang="en">
<head>
<meta charset="utf-8">
<title>RWT Fittings Ltd — Business Cards</title>
<link rel="stylesheet" href="https://fonts.googleapis.com/css2?family=Open+Sans:wght@400;600;700&display=swap">
<style>
  :root {
    --bg-light: #5a5a5a;
    --bg-dark: #121212;
    --card: #1c1c1e;
    --card-back: #1a1a1b;
    --card-edge: #0d0d0e;
    --accent: #29a9e0;
    --text: #e4e4e4;
    --text-soft: #cfcfcf;
    --watermark: #2a2a2d;
    --emboss: #45454a;
  }
  * { box-sizing: border-box; margin: 0; padding: 0; }
  html, body { width: 1200px; height: 780px; overflow: hidden; }
  body {
    background: linear-gradient(160deg, var(--bg-light) 0%, #2e2e2e 55%, var(--bg-dark) 100%);
    font-family: "Open Sans", Arial, sans-serif;
    position: relative;
  }
  .card {
    position: absolute;
    top: 235px;
    width: 540px;
    height: 310px;
    border-radius: 24px;
    overflow: hidden;
    box-shadow: 0 6px 0 var(--card-edge), 0 22px 40px rgba(0,0,0,.55);
  }
  .card--front { left: 45px; background: var(--card); padding: 34px 40px; }
  .card--back  { left: 615px; background: var(--card-back); display: flex; align-items: center; justify-content: center; }

  .front-content { position: relative; z-index: 1; }

  .watermark {
    position: absolute;
    right: 34px;
    bottom: 36px;
    display: flex;
    flex-direction: column;
    align-items: flex-end;
    gap: 10px;
  }
  .watermark__mark { width: 70px; height: 70px; background: var(--watermark); }
  .watermark__name {
    color: var(--watermark);
    font-weight: 700;
    font-size: 28px;
    line-height: 1.1;
    text-align: right;
  }

  .brand { display: flex; align-items: center; gap: 12px; }
  .brand__mark { width: 22px; height: 22px; background: var(--accent); }
  .brand__name { color: var(--accent); font-weight: 700; font-size: 30px; letter-spacing: .5px; }

  .person { margin-top: 26px; display: flex; gap: 12px; }
  .person__bar { width: 10px; height: 44px; background: var(--accent); }
  .person__name { color: var(--accent); font-weight: 600; font-size: 22px; text-transform: uppercase; line-height: 1.1; }
  .person__title { color: var(--text); font-size: 15px; margin-top: 3px; }

  .address { color: var(--text); font-size: 15px; line-height: 1.4; margin-top: 16px; }

  .contacts { list-style: none; margin-top: 14px; }
  .contacts li { display: flex; align-items: center; gap: 8px; color: var(--text-soft); font-size: 15px; line-height: 1.55; }
  .contacts svg { width: 13px; height: 13px; fill: var(--accent); flex: none; }

  .back-brand { display: flex; align-items: center; gap: 18px; }
  .back-brand__mark { width: 40px; height: 40px; background: var(--emboss); }
  .back-brand__name { color: var(--emboss); font-weight: 700; font-size: 46px; letter-spacing: 1px; }
</style>
</head>
<body>

  <section class="card card--front" aria-label="Business card front">
    <div class="watermark" aria-hidden="true">
      <span class="watermark__mark"></span>
      <span class="watermark__name">RWT<br>Fittings Ltd</span>
    </div>

    <div class="front-content">
      <div class="brand">
        <span class="brand__mark"></span>
        <span class="brand__name">RWT Fittings Ltd</span>
      </div>

      <div class="person">
        <span class="person__bar"></span>
        <div>
          <p class="person__name">Marco Peltieri</p>
          <p class="person__title">Owner &amp; Manager</p>
        </div>
      </div>

      <p class="address">1407-5194 Linden Row<br>Burnaby BC, V5H 2K9</p>

      <ul class="contacts">
        <li>
          <svg viewBox="0 0 24 24" aria-hidden="true"><path d="M6.6 10.8a15.1 15.1 0 0 0 6.6 6.6l2.2-2.2a1 1 0 0 1 1-.25 11.4 11.4 0 0 0 3.6.57 1 1 0 0 1 1 1V20a1 1 0 0 1-1 1A17 17 0 0 1 3 4a1 1 0 0 1 1-1h3.5a1 1 0 0 1 1 1c0 1.25.2 2.45.57 3.57a1 1 0 0 1-.25 1z"/></svg>
          16045518293
        </li>
        <li>
          <svg viewBox="0 0 24 24" aria-hidden="true"><path d="M2 5h20v14H2z M2 5l10 8 10-8"/></svg>
          RWTFittings@mailbox-demo.com
        </li>
        <li>
          <svg viewBox="0 0 24 24" aria-hidden="true"><circle cx="12" cy="12" r="10"/></svg>
          www.rwtfittings-demo.com
        </li>
      </ul>
    </div>
  </section>

  <section class="card card--back" aria-label="Business card back">
    <div class="back-brand">
      <span class="back-brand__mark"></span>
      <span class="back-brand__name">RWT Fittings Ltd</span>
    </div>
  </section>

</body>
</html>
```